Construction material supplies company business card ****

1. Full company name “K T Masonry Works Ltd”
I am after a Business card design for the company as a whole. We are better known in Solomon Islands as “K T Masonry” for short.

We are a building materials supplier of
Ready Mixed Concrete, Bricks and Blocks,
Quarry products- gravel, aggregates, sand etc.
Cement distributor/retailer of reputable brands.
Other prefab concrete products. Culverts, wave breakers, concrete retaining blocks etc.

2. Competitive Advantage over Competition: Quality, efficient, professional, dependable, reliable

3. We want people to feel trust worthy, high quality, strong when they see our brand

5. No preference to color. Maybe more sturdy and corporate. Not fancy.

Industry/Entity Type

CONSTRUCTION SUPPLY

Contact Information for Business Card

Name, Position, office phone mob phone, email

Requirements
Must have
• the company logo
Nice to have
• would like to see a mixture of designs, of with logo only and also with simple graphic designs to bring out the company whilst still have the strong sturdy professional feeling

```html
<!DOCTYPE html>
<html lang="en">
<head>
<meta charset="utf-8">
<title>K T Masonry – Business Card</title>
<link href="https://fonts.googleapis.com/css2?family=Roboto:wght@400;700&display=swap" rel="stylesheet">
<style>
  :root {
    --backdrop: #2a2a2a;
    --card-light: #ececec;
    --card-mid: #d9d9d9;
    --navy: #1d3d63;
    --band: #2c5075;
    --band-text: #e8eef5;
  }
  * { margin: 0; padding: 0; box-sizing: border-box; }
  html, body { width: 1200px; height: 1138px; overflow: hidden; }
  body {
    background: var(--backdrop);
    font-family: "Roboto", Arial, sans-serif;
    color: var(--navy);
    position: relative;
  }
  .card {
    position: absolute;
    width: 620px;
    height: 375px;
    border-radius: 16px;
    background: radial-gradient(ellipse at 40% 40%, var(--card-light), var(--card-mid));
    overflow: hidden;
  }
  .card--front { left: 274px; top: 186px; }
  .card--back { left: 276px; top: 608px; }

  .brand {
    position: absolute;
    font-weight: 700;
    color: var(--navy);
    letter-spacing: 1px;
    white-space: nowrap;
    display: flex;
    align-items: center;
  }
  .brand__square { background: var(--navy); display: inline-block; }
  .brand--front { left: 82px; top: 66px; font-size: 52px; gap: 22px; }
  .brand--front .brand__square { width: 58px; height: 58px; }
  .brand--back { right: 32px; top: 52px; font-size: 36px; gap: 16px; }
  .brand--back .brand__square { width: 42px; height: 42px; }

  .service-band {
    position: absolute; left: 0; right: 0; top: 213px; height: 79px;
    background: var(--band);
  }
  .service-pill {
    position: absolute; left: 137px; top: 186px; width: 348px; height: 40px;
    background: var(--band); border: 2px solid #f2f2f2; border-radius: 20px;
    color: var(--band-text); font-size: 16px; text-align: center; line-height: 36px;
  }
  .service-list {
    position: absolute; left: 0; right: 0; top: 238px;
    text-align: center; color: var(--band-text); font-size: 16px; line-height: 22px;
  }
  .service-extra {
    position: absolute; left: 0; right: 0; top: 305px;
    text-align: center; color: var(--navy); font-size: 16px; line-height: 24px;
  }

  .person { position: absolute; left: 30px; top: 188px; }
  .person__name { font-size: 24px; font-weight: 700; }
  .person__role { font-size: 16px; margin-top: 2px; }
  .divider { position: absolute; left: 0; top: 0; }
  .contacts { position: absolute; left: 30px; top: 270px; list-style: none; font-size: 17px; }
  .contacts li { display: flex; align-items: center; height: 26px; }
  .contacts svg { width: 14px; height: 14px; margin: 0 17px 0 2px; fill: var(--navy); }
  .address {
    position: absolute; right: 30px; top: 294px;
    text-align: right; font-size: 17px; line-height: 26px;
  }
</style>
</head>
<body>
  <section class="card card--front">
    <div class="brand brand--front"><span class="brand__square"></span>K T MASONRY</div>
    <div class="service-band"></div>
    <div class="service-pill">We are a building materials supplier of</div>
    <p class="service-list">Ready Mixed Concrete, Bricks and Blocks, Quarry Products<br>Quarry Products:- Gravel, Aggregates, Sand Etc.</p>
    <p class="service-extra">Cement Distributor/Retailer of Reputable Brands.<br>Other Concrete Products Culverts, Wave Breakers, Concrete Retaining Blocks</p>
  </section>

  <section class="card card--back">
    <div class="brand brand--back"><span class="brand__square"></span>K T MASONRY</div>
    <div class="person">
      <div class="person__name">Daniel Moreau</div>
      <div class="person__role">Managing Director</div>
    </div>
    <svg class="divider" width="620" height="375" viewBox="0 0 620 375">
      <path d="M30 255 H310 C340 255 345 273 375 273 H588" fill="none" stroke="#1d3d63" stroke-width="1.5"/>
    </svg>
    <ul class="contacts">
      <li><svg viewBox="0 0 16 16"><path d="M2 5c0-2 3-3 6-3s6 1 6 3v1h-3V4.5H5V6H2z M4 7h8l2 7H2z"/></svg>000 0000 0000</li>
      <li><svg viewBox="0 0 16 16"><path d="M1 3h14v10H1z M2 4l6 5 6-5" stroke="#ececec" stroke-width="1"/></svg>daniel@ktmasonry.com</li>
      <li><svg viewBox="0 0 16 16"><circle cx="8" cy="8" r="7"/><path d="M1 8h14M8 1v14M3 4h10M3 12h10" stroke="#ececec" stroke-width="1" fill="none"/></svg>www.ktmasonry.com</li>
    </ul>
    <p class="address">234 Anywhere St., Any City,<br>Any Town, US 123456</p>
  </section>
</body>
</html>
```